AGP letterhead

We need a letterhead design for our new company based in Los Angeles called "Amber Gate Pictures". We develop film and television projects. We work with investors, financiers, film production companies, film distribution and sales companies as well as studios. We would like to incorporate our logo (see attached) but make the letterhead simple and elegant. We need to include: logo, company address, phone number and company website.
Updates

Hello designers, Thanks for your submissions. For our letterhead, we are looking for something more simple and elegant. No heavy bars or lines. Make it feel light and clean. Not a lot of ink on the page. Use the logo and contact info but think "clean", "streamlined" and mostly white paper. Looking forward to seeing more... thanks! Amber Gate Pictures team

Target Market(s)

Studio executives, talent agents and agencies, financiers, investors.

Industry/Entity Type

It Company

Requirements
Must have
• Amber Gate Pictures logo (see attached). Logo may be cropped and altered appropriately for elegant letterhead design.
• Please include:
• COMPANY ADDRESS:
• Tolvane Arts Park
• 2850 Delmore Street
• Crest Hall, 2nd Floor
• Larkmoor Bay, CA 90412
• COMPANY WEBSITE:
• www.ambergatepicturesco.example
• COMPANY PHONE NUMBER:
• 555-604-2187

```html
<!DOCTYPE html>
<html lang="en">
<head>
<meta charset="utf-8">
<title>Amber Gate Pictures — Letterhead</title>
<link rel="stylesheet" href="https://fonts.googleapis.com/css2?family=Source+Sans+3:wght@400;600&display=swap">
<style>
  :root {
    --paper: #ffffff;
    --ink: #4a4a4a;
    --brand-blue: #1f86bd;
    --mark-dark: #0b1820;
    --wave-grey: #c9c9cb;
    --icon-grey: #6a6a6a;
  }
  html, body {
    margin: 0;
    padding: 0;
    width: 950px;
    height: 1200px;
    overflow: hidden;
    background: var(--paper);
  }
  .letterhead {
    position: relative;
    width: 950px;
    height: 1200px;
    background: var(--paper);
    font-family: "Source Sans 3", "Myriad Pro", Arial, sans-serif;
    color: var(--ink);
  }
  .brand {
    position: absolute;
    top: 28px;
    left: 0;
    width: 950px;
    display: flex;
    flex-direction: column;
    align-items: center;
  }
  .brand-disc {
    width: 132px;
    height: 132px;
    border-radius: 50%;
    background: var(--mark-dark);
  }
  .brand-name {
    margin-top: 14px;
    font-size: 25px;
    font-weight: 600;
    letter-spacing: 2px;
    text-transform: uppercase;
    color: var(--brand-blue);
  }
  .footer-wave {
    position: absolute;
    left: 0;
    top: 1036px;
    width: 950px;
    height: 110px;
  }
  .contact {
    position: absolute;
    right: 26px;
    top: 1078px;
    text-align: right;
    font-size: 16.5px;
    line-height: 1.4;
    font-style: normal;
  }
  .contact-line {
    display: flex;
    justify-content: flex-end;
    align-items: center;
    gap: 6px;
    margin-bottom: 8px;
  }
  .contact-icon {
    width: 15px;
    height: 15px;
  }
  .address {
    margin-top: 4px;
  }
</style>
</head>
<body>
  <main class="letterhead">
    <header class="brand">
      <div class="brand-disc" aria-hidden="true"></div>
      <div class="brand-name">Amber Gate Pictures</div>
    </header>

    <svg class="footer-wave" viewBox="0 0 950 110" aria-hidden="true">
      <path d="M0 90 C 180 112, 360 90, 560 54 C 700 30, 820 22, 950 20 L 950 32 C 820 34, 700 42, 560 64 C 360 98, 180 120, 0 100 Z" fill="var(--wave-grey)"/>
    </svg>

    <address class="contact">
      <div class="contact-line">
        <svg class="contact-icon" viewBox="0 0 16 16" aria-hidden="true">
          <circle cx="8" cy="8" r="7" fill="none" stroke="var(--icon-grey)" stroke-width="1"/>
          <path d="M5.5 4.5 L7 4 L7.8 6.3 L6.8 7 C7.2 8 8 8.8 9 9.2 L9.7 8.2 L12 9 L11.5 10.5 C8 11 5 8 5.5 4.5 Z" fill="var(--icon-grey)"/>
        </svg>
        <span class="phone">555-604-2187</span>
      </div>
      <div class="contact-line">
        <svg class="contact-icon" viewBox="0 0 16 16" aria-hidden="true">
          <circle cx="8" cy="8" r="6.5" fill="none" stroke="var(--icon-grey)" stroke-width="1"/>
          <ellipse cx="8" cy="8" rx="3" ry="6.5" fill="none" stroke="var(--icon-grey)" stroke-width="0.9"/>
          <line x1="1.5" y1="8" x2="14.5" y2="8" stroke="var(--icon-grey)" stroke-width="0.9"/>
          <line x1="2.5" y1="5" x2="13.5" y2="5" stroke="var(--icon-grey)" stroke-width="0.8"/>
          <line x1="2.5" y1="11" x2="13.5" y2="11" stroke="var(--icon-grey)" stroke-width="0.8"/>
        </svg>
        <span class="website">www.ambergatepicturesco.example</span>
      </div>
      <div class="address">
        Tolvane Arts Park 2850 Delmore Street Crest Hall,<br>
        2nd Floor Larkmoor Bay, CA 90412
      </div>
    </address>
  </main>
</body>
</html>
```